Corporate Business Card

Very professional, Modern, Not to busy, include phone address email, website
(253) 617-4930, 18761 52nd Avenue S, Kent, WA 98047, martin@plumlinegroup.com, varkoworks.com

Target Market(s)

Manufacturing

Industry/Entity Type

Aero, machining, manufacturing, Off road racing

Contact Information for Business Card

Phone, address email, website

```html
<!DOCTYPE html>
<html lang="en">
<head>
<meta charset="utf-8">
<title>Varko Works – Business Card</title>
<link rel="stylesheet" href="https://fonts.googleapis.com/css2?family=Exo+2:wght@400;500;700;800&display=swap">
<style>
  :root {
    --navy: #16356b;
    --red: #d2232a;
    --paper: #ffffff;
    --backdrop: #e9e9e9;
    --rule: #b9b9b9;
  }
  * { margin: 0; padding: 0; box-sizing: border-box; }
  html, body { width: 1065px; height: 1200px; overflow: hidden; background: var(--backdrop); }
  body { position: relative; font-family: "Exo 2", sans-serif; color: var(--navy); }

  .card { position: absolute; width: 583px; height: 362px; }
  .card-front {
    left: 292px; top: 218px;
    background: var(--paper);
    border-radius: 0 181px 181px 0;
  }
  .card-back {
    left: 263px; top: 623px;
    background: var(--navy);
    border-radius: 181px 0 0 181px;
  }

  .brand-vertical {
    position: absolute;
    left: 70px; top: 66px;
    width: 64px; height: 230px;
    display: flex; align-items: center; justify-content: center;
  }
  .brand-vertical span {
    display: block;
    transform: rotate(-90deg);
    white-space: nowrap;
    font-weight: 800;
    font-size: 34px;
    letter-spacing: 1px;
    color: var(--navy);
  }
  .divider {
    position: absolute;
    left: 169px; top: 94px;
    width: 1px; height: 174px;
    background: var(--rule);
  }

  .details { position: absolute; left: 191px; top: 92px; }
  .person-name { font-weight: 700; font-size: 20px; line-height: 22px; letter-spacing: 0.2px; }
  .person-role { color: var(--red); font-size: 16px; line-height: 18px; font-weight: 400; }

  .contact-list { list-style: none; margin-top: 16px; }
  .contact-list li {
    display: flex; align-items: center;
    font-size: 16px; line-height: 21px;
    letter-spacing: 0.3px;
  }
  .contact-list svg { width: 16px; height: 16px; margin-right: 5px; flex: none; fill: var(--red); }
  .contact-list .address { align-items: flex-start; margin-top: 13px; }
  .contact-list .address svg { width: 17px; height: 24px; margin-top: 1px; }

  .brand-centered {
    position: absolute;
    left: 0; right: 0; top: 150px;
    text-align: center;
    font-weight: 800;
    font-size: 42px;
    letter-spacing: 1.5px;
    color: var(--paper);
  }
</style>
</head>
<body>

<section class="card card-front" aria-label="Business card front">
  <div class="brand-vertical"><span>VARKO WORKS</span></div>
  <div class="divider"></div>
  <div class="details">
    <p class="person-name">DANIEL REYES</p>
    <p class="person-role">Managing Director</p>
    <ul class="contact-list">
      <li>
        <svg viewBox="0 0 24 24" aria-hidden="true"><path d="M6.6 10.8a15.1 15.1 0 0 0 6.6 6.6l2.2-2.2c.3-.3.7-.4 1-.2 1.1.4 2.3.6 3.6.6.6 0 1 .4 1 1V20c0 .6-.4 1-1 1A17 17 0 0 1 3 4c0-.6.4-1 1-1h3.5c.6 0 1 .4 1 1 0 1.3.2 2.5.6 3.6.1.3 0 .7-.2 1z"/></svg>
        (253) 617-4930
      </li>
      <li>
        <svg viewBox="0 0 24 24" aria-hidden="true"><path d="M2 5h20v14H2zM3.5 6.5 12 13l8.5-6.5v-.1h-17zM3.5 8.3v9.2h17V8.3L12 14.8z"/></svg>
        martin@plumlinegroup.com
      </li>
      <li>
        <svg viewBox="0 0 24 24" aria-hidden="true"><path d="M12 2a10 10 0 1 0 0 20 10 10 0 0 0 0-20zm6.9 6h-2.8a15 15 0 0 0-1.4-3.6A8 8 0 0 1 18.9 8zM12 4c.8 1.2 1.5 2.5 1.9 4h-3.8c.4-1.5 1.1-2.8 1.9-4zM4.3 14a8 8 0 0 1 0-4h3.3a16 16 0 0 0 0 4zm.8 2h2.8c.3 1.3.8 2.5 1.4 3.6A8 8 0 0 1 5.1 16zm2.8-8H5.1a8 8 0 0 1 4.2-3.6C8.7 5.5 8.2 6.7 7.9 8zM12 20c-.8-1.2-1.5-2.5-1.9-4h3.8c-.4 1.5-1.1 2.8-1.9 4zm2.3-6H9.7a14 14 0 0 1 0-4h4.6a14 14 0 0 1 0 4zm.4 5.6c.6-1.1 1.1-2.3 1.4-3.6h2.8a8 8 0 0 1-4.2 3.6zm1.7-5.6a16 16 0 0 0 0-4h3.3a8 8 0 0 1 0 4z"/></svg>
        www.varkoworks.com
      </li>
      <li class="address">
        <svg viewBox="0 0 17 24" aria-hidden="true"><path d="M8.5 0A8.5 8.5 0 0 0 0 8.5C0 14 8.5 24 8.5 24S17 14 17 8.5A8.5 8.5 0 0 0 8.5 0zm0 11.2a2.7 2.7 0 1 1 0-5.4 2.7 2.7 0 0 1 0 5.4z"/></svg>
        <span>18761 52nd Avenue S<br>Kent, WA 98047</span>
      </li>
    </ul>
  </div>
</section>

<section class="card card-back" aria-label="Business card back">
  <p class="brand-centered">VARKO WORKS</p>
</section>

</body>
</html>
```